Design and Renovation Company Luxury Business Card

I want to create a luxury business card for a Design and Renovation Firm . We will use our current logo. The company name is 528BUILDA. We do not want anything standard. We need a very unique concept.
Please see uploaded inspiration. I really like the textured paper option. I would like the card to be thick with debossing, and/or embossing options. The logo has orange in it but I would like to see the card with and without the orange. I think the orange may make the company feel less high-end. The goal is to elevate the logo not match its vibe per se of the logo. We want something very unique, not standard at all!
I would like a space for :
Logo,
Name,
Position,
Email,
Office number,
Website Address,
Business Address,
Thank you!
Have fun!
Target Market(s)
Home owners Age 35 +
Industry/Entity Type
Design and Renovation
Contact Information for Business Card
Logo, Name, Position, Email, Office number, Website Address, Business Address,.
Colors
Designer to choose colors to be used in the design.
Requirements
Must have
- A luxury designer feel. Must be black or dark grey but open to other luxury ideas.
Nice to have
- Gold, silver, black embossing or debossing. Textured paper design.
Should not have
- A cheap look and feel.

```html
<!DOCTYPE html>
<html lang="en">
<head>
<meta charset="UTF-8">
<title>528BUILDA Business Card</title>
<link href="https://fonts.googleapis.com/css2?family=Roboto:wght@400;500&family=Roboto+Condensed:wght@700&display=swap" rel="stylesheet">
<style>
  :root {
    --bg: #1b1b1c;
    --card: #333334;
    --card-dark: #2a2a2b;
    --orange: #e8961f;
    --white: #f2f2f2;
    --band: #efefef;
    --ink: #2b2b2b;
    --divider: #555;
  }
  * { margin: 0; padding: 0; box-sizing: border-box; }
  html, body { width: 1200px; height: 840px; overflow: hidden; }
  body {
    background: var(--bg);
    font-family: "Roboto", Arial, sans-serif;
    position: relative;
  }
  .card {
    position: absolute;
    top: 265px;
    width: 540px;
    height: 310px;
    border-radius: 22px;
    background: linear-gradient(160deg, var(--card) 0%, var(--card-dark) 100%);
    border: 2px solid var(--orange);
    overflow: hidden;
  }
  .card-front { left: 40px; }
  .card-back { left: 620px; }

  .brand-name {
    position: absolute;
    font-family: "Roboto", Arial, sans-serif;
    font-weight: 500;
    color: var(--white);
    line-height: 1;
    white-space: nowrap;
  }
  .card-front .brand-name {
    left: 50%;
    top: 50%;
    transform: translate(-50%, -50%);
    font-size: 46px;
  }
  .card-back .brand-name {
    right: 40px;
    top: 50px;
    font-size: 50px;
  }

  .person {
    position: absolute;
    right: 40px;
    top: 128px;
    text-align: right;
  }
  .person-name {
    font-family: "Roboto Condensed", "Arial Narrow", sans-serif;
    font-weight: 700;
    font-size: 19px;
    color: var(--orange);
    letter-spacing: 0.3px;
  }
  .person-role {
    color: var(--white);
    font-size: 13px;
    margin-top: 1px;
  }

  .info-band {
    position: absolute;
    left: 150px;
    right: 0;
    top: 186px;
    height: 84px;
    background: var(--band);
    display: flex;
    align-items: center;
  }
  .address {
    width: 170px;
    text-align: center;
    color: var(--ink);
    font-size: 13px;
    line-height: 1.35;
  }
  .band-divider {
    width: 1px;
    height: 52px;
    background: var(--divider);
  }
  .contact-list {
    list-style: none;
    flex: 1;
    padding-right: 16px;
    color: var(--ink);
    font-size: 12.5px;
    line-height: 1.55;
  }
  .contact-list li {
    display: flex;
    justify-content: flex-end;
    align-items: center;
    gap: 6px;
  }
  .contact-icon { width: 12px; height: 12px; flex-shrink: 0; }
</style>
</head>
<body>

  <section class="card card-front" aria-label="Card front">
    <p class="brand-name">528BUILDA</p>
  </section>

  <section class="card card-back" aria-label="Card back">
    <p class="brand-name">528BUILDA</p>

    <div class="person">
      <p class="person-name">DANIEL HARROW</p>
      <p class="person-role">Manager</p>
    </div>

    <div class="info-band">
      <p class="address">Your Address, City<br>State, Zip 0000</p>
      <span class="band-divider"></span>
      <ul class="contact-list">
        <li>555-014-7392
          <svg class="contact-icon" viewBox="0 0 12 12" aria-hidden="true">
            <path d="M2.5 1 L4.5 1 L5.3 3.4 L4 4.3 Q5 6.8 7.7 8 L8.6 6.7 L11 7.5 L11 9.5 Q11 11 9.5 11 Q1 10 1 2.5 Q1 1 2.5 1 Z" fill="var(--orange)"/>
          </svg>
        </li>
        <li>youremail@mailnest.com
          <svg class="contact-icon" viewBox="0 0 12 12" aria-hidden="true">
            <rect x="0.5" y="2.5" width="11" height="7.5" rx="1" fill="var(--orange)"/>
            <polyline points="1,3 6,7 11,3" fill="none" stroke="var(--band)" stroke-width="1"/>
          </svg>
        </li>
        <li>www.yourwebsite.com
          <svg class="contact-icon" viewBox="0 0 12 12" aria-hidden="true">
            <circle cx="6" cy="6" r="5.5" fill="var(--orange)"/>
            <ellipse cx="6" cy="6" rx="2.2" ry="5.5" fill="none" stroke="var(--band)" stroke-width="0.8"/>
            <line x1="0.5" y1="6" x2="11.5" y2="6" stroke="var(--band)" stroke-width="0.8"/>
          </svg>
        </li>
      </ul>
    </div>
  </section>

</body>
</html>
```